Business Card for my New Brokerage

Looking to get a business card design for my new Real Estate Brokerage.
I want it with Picture, Phone Number, Email, Website, Office Address
Name and Designation. Please add logo too.

Target Market(s)

Real Estate Investors or Home Buyers

Industry/Entity Type

Real Estate

Contact Information for Business Card

Name, Email, Phone Number, website, email, office address

Colors
EB3D1F
EC4F4E
F09395
F8D3D4
FCEDEE

Requirements
Must have
• Minimalistic, Clean, Modern, Photo
Nice to have
• White and Red Colors

```html
<!DOCTYPE html>
<html lang="en">
<head>
<meta charset="utf-8">
<title>Harbor Lane Realty – Business Card</title>
<link href="https://fonts.googleapis.com/css2?family=Montserrat:wght@400;500;600;700&display=swap" rel="stylesheet">
<style>
  :root {
    --brand-red: #d90a0a;
    --soft-pink: #f09395;
    --paper: #ffffff;
    --gold: #d6b25c;
    --backdrop: #1e1e20;
    --photo-top: #e9e4df;
    --photo-bottom: #2d3442;
  }
  * { margin: 0; padding: 0; box-sizing: border-box; }
  html, body { width: 1200px; height: 900px; overflow: hidden; }
  body {
    background: var(--backdrop);
    font-family: "Montserrat", sans-serif;
    display: flex;
    flex-direction: column;
    align-items: center;
    justify-content: center;
    gap: 40px;
  }
  .card {
    position: relative;
    width: 700px;
    height: 400px;
    border-radius: 22px;
    overflow: hidden;
    box-shadow: 0 14px 30px rgba(0,0,0,.45);
  }
  .card-front { background: var(--paper); }
  .card-front .wave { position: absolute; inset: 0; }
  .brand-name {
    color: var(--brand-red);
    font-weight: 700;
    text-transform: uppercase;
    line-height: 1.05;
  }
  .card-front .brand-name {
    position: absolute;
    left: 48px;
    top: 40px;
    font-size: 42px;
  }
  .portrait {
    position: absolute;
    left: 450px;
    top: 34px;
    width: 170px;
    height: 170px;
    border-radius: 50%;
    border: 3px solid var(--brand-red);
    background: linear-gradient(180deg, var(--photo-top) 0%, var(--photo-top) 45%, var(--photo-bottom) 100%);
  }
  .address {
    position: absolute;
    left: 40px;
    top: 300px;
    color: var(--paper);
    font-size: 15px;
    font-weight: 500;
    line-height: 1.45;
  }
  .contact {
    position: absolute;
    right: 40px;
    top: 232px;
    text-align: right;
    color: var(--paper);
  }
  .person-name { font-size: 24px; font-weight: 700; letter-spacing: 1px; text-transform: uppercase; line-height: 1.2; }
  .person-title { font-size: 15px; font-weight: 500; margin-bottom: 6px; }
  .contact-line {
    display: flex;
    justify-content: flex-end;
    align-items: center;
    gap: 8px;
    font-size: 14px;
    font-weight: 500;
    line-height: 1.5;
  }
  .contact-line svg { width: 13px; height: 13px; }
  .card-back {
    background: var(--brand-red);
    display: flex;
    align-items: center;
    justify-content: center;
  }
  .card-back .brand-name {
    color: var(--soft-pink);
    font-size: 72px;
    text-align: center;
  }
</style>
</head>
<body>
  <section class="card card-front">
    <svg class="wave" viewBox="0 0 700 400" preserveAspectRatio="none" aria-hidden="true">
      <path d="M0,118 C40,170 70,210 200,218 C300,224 380,214 470,205 C560,196 640,186 700,150 L700,400 L0,400 Z" fill="var(--brand-red)"/>
      <path d="M0,132 C40,184 80,222 200,230 C300,236 380,228 440,222" fill="none" stroke="var(--gold)" stroke-width="4"/>
      <path d="M612,200 C650,192 680,182 700,170" fill="none" stroke="var(--gold)" stroke-width="5"/>
    </svg>

    <h2 class="brand-name">Harbor Lane<br>Realty</h2>

    <div class="portrait" role="img" aria-label="Portrait photo of the broker"></div>

    <p class="address">1820 Maple Ridge Court<br>Fairhaven, GA 31000</p>

    <div class="contact">
      <h1 class="person-name">Daniel Moreno</h1>
      <p class="person-title">Founder and President</p>
      <p class="contact-line">+330 555-0142
        <svg viewBox="0 0 16 16"><path d="M4 1l3 3-2 2c1 2 3 4 5 5l2-2 3 3-2 3C7 15 1 9 1 3z" fill="var(--paper)"/></svg>
      </p>
      <p class="contact-line">hello@harborlanerealty.com
        <svg viewBox="0 0 16 16"><rect x="1.5" y="3.5" width="13" height="9" fill="none" stroke="var(--paper)" stroke-width="1.5"/><path d="M2 4l6 5 6-5" fill="none" stroke="var(--paper)" stroke-width="1.5"/></svg>
      </p>
      <p class="contact-line">www.harborlanerealty.com
        <svg viewBox="0 0 16 16"><circle cx="8" cy="8" r="6.5" fill="none" stroke="var(--paper)" stroke-width="1.3"/><ellipse cx="8" cy="8" rx="3" ry="6.5" fill="none" stroke="var(--paper)" stroke-width="1.1"/><path d="M1.5 8h13" stroke="var(--paper)" stroke-width="1.1"/></svg>
      </p>
    </div>
  </section>

  <section class="card card-back">
    <h2 class="brand-name">Harbor Lane<br>Realty</h2>
  </section>
</body>
</html>
```